Exclusive Crestline Groomers Invite that connects barbers

I am looking for a general invitation to join a secret club of people that shave their head. I want it the size of a business card that I can hand out to people I see on the street. I want it to feel like a special exclulisve invite to a club that only they can be apart of and want to tell their friends about.

Target Market(s)

35-60 male

Industry/Entity Type

Hair

Contact Information for Business Card

I want it to look like an invite to a secret club that only people that shave their head can be apart of... I will hand it out to people that I think fir our demographic.

Font styles to use
Serif

Colors

Designer to choose colors to be used in the design.

Requirements
Must have
• A feel of exclusivity
• website address (www.crestlinegroomers.example)
• logo

```html
<!DOCTYPE html>
<html lang="en">
<head>
<meta charset="utf-8">
<title>Crestline Groomers – Invitation Card</title>
<link rel="stylesheet" href="https://fonts.googleapis.com/css2?family=Michroma&display=swap">
<style>
  :root {
    --backdrop: #ece7df;
    --card-black: #1d1d1d;
    --card-tan: #e2c29f;
    --card-tan-light: #f4e2cd;
    --ink: #1b1b1b;
    --gold-text: #d9b48c;
  }
  * { margin: 0; padding: 0; box-sizing: border-box; }
  html, body {
    width: 1200px;
    height: 800px;
    overflow: hidden;
    background: var(--backdrop);
  }
  .canvas {
    position: relative;
    width: 1200px;
    height: 800px;
    display: flex;
    align-items: center;
    justify-content: center;
    gap: 40px;
  }
  .card {
    position: relative;
    width: 540px;
    height: 308px;
    border-radius: 4px;
    overflow: hidden;
    box-shadow: 0 6px 18px rgba(0, 0, 0, 0.18);
    font-family: "Michroma", "Arial", sans-serif;
  }
  .card--back {
    background: var(--card-black);
    display: flex;
    align-items: center;
    justify-content: center;
  }
  .card__url {
    color: var(--gold-text);
    font-size: 17px;
    letter-spacing: 0.5px;
  }
  .card--front {
    background: radial-gradient(circle at 45% 40%, var(--card-tan-light) 0%, var(--card-tan) 55%);
  }
  .corner-stripes {
    position: absolute;
    width: 120px;
    height: 120px;
  }
  .corner-stripes--top-right { top: 0; right: 0; }
  .corner-stripes--bottom-left { bottom: 0; left: 0; transform: rotate(180deg); }
  .brand {
    position: absolute;
    left: 0;
    right: 0;
    top: 78px;
    display: flex;
    flex-direction: column;
    align-items: center;
    gap: 22px;
  }
  .brand__mark {
    width: 64px;
    height: 64px;
    border: 3px solid var(--ink);
    border-radius: 4px;
  }
  .brand__name {
    color: var(--ink);
    font-size: 27px;
    letter-spacing: 0.5px;
    white-space: nowrap;
  }
</style>
</head>
<body>
  <main class="canvas">
    <section class="card card--back" aria-label="Card back">
      <p class="card__url">www.crestlinegroomers.example</p>
    </section>

    <section class="card card--front" aria-label="Card front">
      <svg class="corner-stripes corner-stripes--top-right" viewBox="0 0 120 120" aria-hidden="true">
        <polygon points="0,0 34,0 34,34" fill="var(--ink)"/>
        <g stroke="var(--ink)" stroke-width="8">
          <line x1="46" y1="0" x2="120" y2="74"/>
          <line x1="62" y1="0" x2="120" y2="58"/>
          <line x1="78" y1="0" x2="120" y2="42"/>
          <line x1="94" y1="0" x2="120" y2="26"/>
        </g>
      </svg>
      <svg class="corner-stripes corner-stripes--bottom-left" viewBox="0 0 120 120" aria-hidden="true">
        <polygon points="0,0 34,0 34,34" fill="var(--ink)"/>
        <g stroke="var(--ink)" stroke-width="8">
          <line x1="46" y1="0" x2="120" y2="74"/>
          <line x1="62" y1="0" x2="120" y2="58"/>
          <line x1="78" y1="0" x2="120" y2="42"/>
          <line x1="94" y1="0" x2="120" y2="26"/>
        </g>
      </svg>

      <div class="brand">
        <span class="brand__mark" aria-hidden="true"></span>
        <h1 class="brand__name">Crestline Groomers</h1>
      </div>
    </section>
  </main>
</body>
</html>
```